Brivo Hair

Hello - our company Vantor 4 develops novel products for the skin, & hair care industry as well as dietary supplements. We're looking for a label design for a new product. The product is a premium hair loss/growth supplement. Our primary demo is women ages 45-65. I attached the brand logo & some competitive product designs that we find attractive.

I've been traveling & have not had the time to adequately review the designs, please be patient with me.

```html
<!DOCTYPE html>
<html lang="en">
<head>
<meta charset="utf-8">
<title>Brivo Hair – Advance Formula Women Label</title>
<link href="https://fonts.googleapis.com/css2?family=Montserrat:wght@600;700&family=Libre+Baskerville:wght@700&family=Saira+Semi+Condensed:wght@400;700&display=swap" rel="stylesheet">
<style>
  :root {
    --page-bg: #565656;
    --label-black: #050505;
    --gold-dark: #b8862b;
    --gold-light: #f6dc93;
    --gold-mid: #d4a243;
    --silver-light: #f2f2f2;
    --silver-dark: #a9a9a9;
    --brand-blue: #4aa8e0;
    --white: #ffffff;
    --ink: #111111;
  }
  * { margin: 0; padding: 0; box-sizing: border-box; }
  html, body { width: 692px; height: 1200px; overflow: hidden; }
  body { background: var(--page-bg); position: relative; }

  .label {
    position: absolute; left: 46px; top: 211px;
    width: 600px; height: 777px;
    overflow: hidden;
    box-shadow: 0 10px 30px rgba(0,0,0,.45);
  }
  .label-shapes { position: absolute; inset: 0; }

  .company-name {
    position: absolute; left: 0; right: 0; top: 52px;
    text-align: center;
    font-family: "Montserrat", sans-serif; font-weight: 700;
    font-size: 50px; letter-spacing: -1px; color: var(--white);
  }
  .claim {
    position: absolute; left: 0; right: 0; top: 143px;
    text-align: center;
    font-family: "Montserrat", sans-serif; font-weight: 700;
    font-size: 20px; letter-spacing: 1.5px; color: var(--white);
  }
  .extract-box {
    position: absolute; left: 76px; top: 185px; width: 447px; height: 45px;
    border: 1.5px solid var(--gold-mid); border-radius: 3px;
    display: flex; align-items: center; justify-content: center;
    font-family: "Libre Baskerville", serif; font-weight: 700;
    font-size: 22px; letter-spacing: 3px; color: var(--white);
  }
  .product-name {
    position: absolute; left: 0; right: 0; top: 246px;
    text-align: center;
    font-family: "Montserrat", sans-serif; font-weight: 600;
    font-size: 62px; letter-spacing: 3px; color: var(--brand-blue);
  }
  .strength-bar {
    position: absolute; left: 117px; top: 366px; width: 368px; height: 57px;
    background: linear-gradient(180deg, var(--silver-light), var(--silver-dark));
    display: flex; align-items: flex-end; justify-content: center; padding-bottom: 8px;
    font-family: "Libre Baskerville", serif; font-weight: 700;
    font-size: 20px; letter-spacing: 3.5px; color: var(--ink);
  }
  .formula {
    position: absolute; left: 0; right: 0; top: 432px;
    text-align: center;
    font-family: "Libre Baskerville", serif; font-weight: 700;
    font-size: 37px; color: var(--ink);
  }
  .audience {
    position: absolute; left: 0; right: 0; top: 470px;
    text-align: center;
    font-family: "Libre Baskerville", serif; font-weight: 700;
    font-size: 72px; letter-spacing: 1px; color: var(--ink);
  }
  .follicle-art {
    position: absolute; left: 112px; top: 589px; width: 111px; height: 111px;
    border-radius: 50%; border: 2px solid var(--gold-mid);
    background: radial-gradient(circle at 50% 45%, #4a4a4a, #141414 70%);
  }
  .benefits {
    position: absolute; left: 243px; top: 602px; width: 300px;
    list-style: none;
    font-family: "Saira Semi Condensed", sans-serif; font-size: 10.5px;
    line-height: 1.45; color: var(--white);
  }
  .benefits li { position: relative; padding-left: 19px; margin-bottom: 12px; }
  .benefits svg { position: absolute; left: 0; top: 2px; width: 12px; height: 12px; }
  .count-pill {
    position: absolute; left: 205px; top: 703px; width: 191px; height: 34px;
    border-radius: 17px; border: 2px solid var(--gold-mid);
    background: linear-gradient(180deg, var(--silver-light), var(--silver-dark));
    display: flex; align-items: center; justify-content: center;
    font-family: "Saira Semi Condensed", sans-serif; font-weight: 700;
    font-size: 22px; color: var(--ink);
  }
  .category {
    position: absolute; left: 0; right: 0; top: 741px;
    text-align: center;
    font-family: "Saira Semi Condensed", sans-serif; font-weight: 700;
    font-size: 21px; color: var(--ink);
  }
</style>
</head>
<body>
  <div class="label">
    <svg class="label-shapes" viewBox="0 0 600 777" width="600" height="777" aria-hidden="true">
      <defs>
        <linearGradient id="gold" x1="0" y1="0" x2="1" y2="0">
          <stop offset="0" stop-color="#b8862b"/>
          <stop offset=".35" stop-color="#f6dc93"/>
          <stop offset=".65" stop-color="#e6bf6a"/>
          <stop offset="1" stop-color="#c0902f"/>
        </linearGradient>
      </defs>
      <rect width="600" height="777" fill="url(#gold)"/>
      <path d="M0 18 H600 V330 Q300 420 0 330 Z" fill="#050505"/>
      <path d="M0 604 Q300 505 600 604 V720 H0 Z" fill="#050505"/>
      <rect y="718" width="600" height="2" fill="#f6dc93"/>
    </svg>

    <div class="company-name">Vantor 4</div>
    <div class="claim">MEDICALLY PROVEN</div>
    <div class="extract-box">HE SHOULD 12:1 EXTRACT</div>
    <div class="product-name">Brivo Hair</div>
    <div class="strength-bar">CLINICAL STRENGTH</div>
    <div class="formula">ADVANCE FORMULA</div>
    <div class="audience">WOMEN</div>

    <div class="follicle-art" role="img" aria-label="Illustration of a hair follicle in a network of fine lines"></div>

    <ul class="benefits">
      <li>
        <svg viewBox="0 0 12 12"><circle cx="6" cy="6" r="5.2" fill="none" stroke="#d4a243" stroke-width="1"/><path d="M3.4 6.2 L5.3 8 L8.7 4.3" fill="none" stroke="#d4a243" stroke-width="1.2"/></svg>
        Lorem ipsum dolor sit amet, consectetur adipiscing elit, sed do eiusmod tempor incididunt ut labore et dolore magna aliqua.
      </li>
      <li>
        <svg viewBox="0 0 12 12"><circle cx="6" cy="6" r="5.2" fill="none" stroke="#d4a243" stroke-width="1"/><path d="M3.4 6.2 L5.3 8 L8.7 4.3" fill="none" stroke="#d4a243" stroke-width="1.2"/></svg>
        Ut enim ad minim veniam, quis nostrud exercitation ullamco laboris nisi ut
      </li>
    </ul>

    <div class="count-pill">60 CAPSULES</div>
    <div class="category">PREMIUM HAIR LOSS/GROWTH SUPPLEMENT</div>
  </div>
</body>
</html>
```